Marble Orchard - Report on digital habits and attitudes

We are a research company and we have written a PowerPoint Report to present the results of a series of surveys conducted in the last three years. The research is about the "Marble Orchard": people are facing the opportunities and challanges of their lives transformed by the digital technologies. We have investigated a number of topics through thousands of interviews and we've analyzed the data presented in the PowerPoint document.
We're not quite satisfied with the look and feel of the report: it looks too flat and boring, too "basic" to be presented as a professional work, yet being just that. We'd like you to upgrade the graphics and style of the report up to the level of a professional research product. The document still needs to be fully editable (either text and charts) but you can rearrange all the contents as you please, adding images, changing font and text size, colors and whatever you think is necessary to reach our goal.

Target Market(s)

Media covering digital issues
Marketing executives
Public institutions and policy makers

Industry/Entity Type

Market Research

Requirements
Must have
• The treats of a professional work
Fully editable within PowerPoint (either text and charts)
Nice to have
• Smart images
Original organization of the pages
Colors and graphics coherent with the quillbrook.it logo/website look and feel
Should not have
• PPT document over 30 MBytes
Images violating copyright

```html
<!DOCTYPE html>
<html lang="it">
<head>
<meta charset="utf-8">
<title>Osservatorio Marble Orchard – Report</title>
<link href="https://fonts.googleapis.com/css2?family=Montserrat:wght@500;600;800&family=Open+Sans:wght@400;600&display=swap" rel="stylesheet">
<style>
  :root{
    --page:#1c1c1c;
    --coral:#de6a52;
    --navy:#14213f;
    --navy-deep:#0d1630;
    --badge:#1f3a6e;
    --gold:#e8a530;
    --gold-soft:#f6d58f;
    --maroon:#7a1230;
    --white:#ffffff;
    --ink:#2a2a2a;
    --grid:#d9d9d9;
  }
  *{box-sizing:border-box;margin:0;padding:0}
  html,body{width:1200px;height:3376px;overflow:hidden;background:var(--page)}
  body{position:relative;font-family:"Montserrat",sans-serif;color:var(--white)}
  .slide{position:absolute;left:51px;width:1098px;height:616px;overflow:hidden}
  .slide-1{top:60px;background:var(--coral)}
  .slide-2{top:720px;background:linear-gradient(115deg,#0c1530 0%,#15265a 48%,#243d86 62%,#3b3f86 78%,#1a2752 100%)}
  .slide-3{top:1380px;background:linear-gradient(120deg,#101c3a 0%,#1a2c52 55%,#1f3560 100%)}
  .slide-4{top:2040px;background:linear-gradient(120deg,#14223f 0%,#1c2c4c 50%,#23365a 100%)}
  .slide-5{top:2700px;background:radial-gradient(ellipse at 50% 30%,#1d3158 0%,#132347 60%,#0d1a38 100%)}
  .page-no{position:absolute;top:0;right:0;width:42px;height:42px;background:var(--badge);
    font:500 17px "Montserrat",sans-serif;display:flex;align-items:center;justify-content:center}

  .brand{position:absolute;display:flex;align-items:center}
  .brand-mark{border-radius:50%;background:var(--gold);border:5px solid var(--navy);flex:none}
  .brand-name{font-weight:800;line-height:.9;letter-spacing:-1px}
  .brand-sub{font-weight:600}
  .brand-small{left:18px;top:18px}
  .brand-small .brand-mark{width:104px;height:104px}
  .brand-small .brand-text{margin-left:12px}
  .brand-small .brand-name{font-size:64px}
  .brand-small .brand-sub{font-size:22px;margin-top:6px}

  .cover-mark{position:absolute;left:21px;top:19px;width:288px;height:288px;border-radius:50%;background:var(--gold);border:14px solid var(--navy)}
  .cover-title{position:absolute;left:326px;top:70px;font-size:128px;font-weight:800;line-height:1;letter-spacing:-2px}
  .cover-sub{position:absolute;left:326px;top:200px;font-size:48px;font-weight:600}
  .cover-photo{position:absolute;left:0;right:0;top:300px;bottom:0;
    background:linear-gradient(180deg,rgba(222,106,82,0) 0%,#c8573f 35%,#8c3a2c 100%)}

  .toc{position:absolute;left:18px;right:16px;top:170px;list-style:none}
  .toc li{position:absolute;left:0;right:0;display:flex;align-items:baseline;font-size:26px;font-weight:600}
  .toc .dots{flex:1;margin:0 10px;border-bottom:3px dotted rgba(255,255,255,.85);transform:translateY(-6px)}

  .tag{position:absolute;left:17px;width:458px;height:59px;background:var(--gold);color:var(--ink);
    clip-path:polygon(0 0,100% 0,94% 100%,0 100%);font-size:36px;font-weight:600;padding-left:14px;line-height:59px}
  .intro-text{position:absolute;left:17px;top:252px;width:540px;font-family:"Open Sans",sans-serif;font-size:11.5px;line-height:26px}
  .intro-text p+p{margin-top:8px}
  .intro-photo{position:absolute;left:594px;top:73px;width:484px;height:527px;
    background:radial-gradient(circle at 55% 30%,#c9d6e2 0%,#7f97ad 35%,#3e5168 70%,#2a3a52 100%)}
  .bg-photo{position:absolute;inset:0;background:radial-gradient(circle at 35% 40%,rgba(80,100,130,.35),rgba(0,0,0,0) 60%)}

  .fear-text{position:absolute;left:17px;top:316px;width:540px;font-family:"Open Sans",sans-serif;font-size:17.5px;line-height:34px}
  .chart{position:absolute;left:594px;top:134px;width:484px;height:442px;background:var(--white)}
  .chart-title{position:absolute;left:8px;top:8px;width:468px;height:55px;background:var(--navy-deep);color:var(--gold);
    font-size:25px;font-weight:500;display:flex;align-items:center;justify-content:center}
  .chart svg{position:absolute;left:0;top:0}

  .closing{position:absolute;left:0;right:0;text-align:center}
  .brand-center{left:322px;top:106px}
  .brand-center .brand-mark{width:104px;height:104px}
  .brand-center .brand-text{margin-left:12px}
  .brand-center .brand-name{font-size:64px}
  .brand-center .brand-sub{font-size:22px;margin-top:6px}
  .thanks{top:222px;font-size:96px;font-weight:800;color:var(--gold);letter-spacing:-2px}
  .closing-text{top:352px;left:26px;right:26px;font-family:"Open Sans",sans-serif;font-size:17px;line-height:43px}
</style>
</head>
<body>

<section class="slide slide-1">
  <div class="cover-mark"></div>
  <h1 class="cover-title">OMO</h1>
  <p class="cover-sub">Osservatorio Marble Orchard</p>
  <div class="cover-photo" role="img" aria-label="Photo of young people leaning on a red wall, smiling at their smartphones"></div>
  <div class="page-no">01</div>
</section>

<section class="slide slide-2">
  <div class="brand brand-small">
    <div class="brand-mark"></div>
    <div class="brand-text"><div class="brand-name">OMO</div><div class="brand-sub">Osservatorio Marble Orchard</div></div>
  </div>
  <ol class="toc">
    <li style="top:0"><span>Capitolo 1</span><span class="dots"></span><span>01</span></li>
    <li style="top:68px"><span>Capitolo 2</span><span class="dots"></span><span>04</span></li>
    <li style="top:128px"><span>Capitolo 3</span><span class="dots"></span><span>10</span></li>
    <li style="top:196px"><span>Capitolo 4</span><span class="dots"></span><span>15</span></li>
    <li style="top:264px"><span>Capitolo 5</span><span class="dots"></span><span>20</span></li>
    <li style="top:325px"><span>Capitolo 6</span><span class="dots"></span><span>24</span></li>
    <li style="top:393px"><span>Capitolo 7</span><span class="dots"></span><span>28</span></li>
  </ol>
  <div class="page-no">02</div>
</section>

<section class="slide slide-3">
  <div class="bg-photo" role="img" aria-label="Dark background photo of hands using devices with floating reaction bubbles"></div>
  <div class="brand brand-small">
    <div class="brand-mark"></div>
    <div class="brand-text"><div class="brand-name">OMO</div><div class="brand-sub">Osservatorio Marble Orchard</div></div>
  </div>
  <h2 class="tag" style="top:160px">Introduzione</h2>
  <div class="intro-text">
    <p>Il digitale ha cambiato il mondo a un livello di profondità di cui non siamo ancora pienamente consapevoli.</p>
    <p>E' facile riconoscere le manifestazioni del digitale nei comportamenti delle persone e notare come ha formato nuove abitudini e ritualità quotidiane.</p>
    <p>Non è altrettanto immediato comprendere quanto il digitale abbia modificato il mondo interiore e abbia inciso sul senso dell'identità, sulle emozioni in gioco nelle relazioni, su affetti e sessualità, sul modo di concepire la società, i diritti e la libertà personale.</p>
    <p>L'obiettivo di questo lavoro di ricerca è raccontare la struttura e l'evoluzione di alcuni atteggiamenti di fondo che influenzano i comportamenti quotidiani legati alle tecnologie digitali. Le informazioni sono ricavate dalle dichiarazioni di campioni di individui chiamati a riflettere sull'ambiente connesso, cioè l'insieme di tutte le relazioni e attività che si possono svolgere grazie alla Rete e, più in generale, grazie a tutte le innovazioni introdotte dagli strumenti e dai servizi digitali.</p>
  </div>
  <div class="intro-photo" role="img" aria-label="Photo of a hand holding a smartphone with glowing notification bubbles"></div>
  <div class="page-no">03</div>
</section>

<section class="slide slide-4">
  <div class="bg-photo" role="img" aria-label="Dark background photo of people holding smartphones"></div>
  <div class="brand brand-small">
    <div class="brand-mark"></div>
    <div class="brand-text"><div class="brand-name">OMO</div><div class="brand-sub">Osservatorio Marble Orchard</div></div>
  </div>
  <h2 class="tag" style="top:233px">Le paure</h2>
  <p class="fear-text">Otto persone su dieci ritengono che nell'ambiente digitale si siano diffuse pratiche di manipolazione delle persone più efficaci rispetto al passato. Il riferimento al passato è relativo al '900, epoca in cui i mezzi di comunicazione di massa, tutti broadcasting, erano gestiti dai governi e dai grandi editori.</p>
  <figure class="chart">
    <figcaption class="chart-title">La manipolazione delle persone</figcaption>
    <svg width="484" height="442" viewBox="0 0 484 442" font-family="Open Sans, sans-serif" font-size="16" fill="#2a2a2a">
      <g stroke="var(--grid)" stroke-width="1">
        <line x1="52" y1="74" x2="52" y2="378"/><line x1="146" y1="74" x2="146" y2="378"/>
        <line x1="242" y1="74" x2="242" y2="378"/><line x1="336" y1="74" x2="336" y2="378"/>
        <line x1="430" y1="74" x2="430" y2="378"/>
        <line x1="8" y1="74" x2="476" y2="74"/><line x1="8" y1="146" x2="476" y2="146"/>
        <line x1="8" y1="220" x2="476" y2="220"/><line x1="8" y1="293" x2="476" y2="293"/>
      </g>
      <line x1="8" y1="378" x2="476" y2="378" stroke="#999" stroke-width="1.5"/>
      <path d="M27,175 C70,185 90,200 113,222 C160,265 205,320 235,313 C270,305 310,200 352,179 C395,160 410,120 458,133" fill="none" stroke="var(--maroon)" stroke-width="2.5"/>
      <g fill="var(--gold)" stroke="var(--gold-soft)" stroke-width="5">
        <circle cx="27" cy="175" r="10"/><circle cx="113" cy="222" r="10"/>
        <circle cx="235" cy="313" r="10"/><circle cx="352" cy="179" r="10"/>
        <circle cx="458" cy="133" r="10"/>
      </g>
      <g>
        <text x="36" y="162">79%</text><text x="122" y="209">78%</text>
        <text x="218" y="296">77%</text><text x="334" y="154">79%</text>
        <text x="440" y="174">80%</text>
      </g>
      <g text-anchor="middle">
        <text x="52" y="408">Feb 19</text><text x="146" y="408">Oct 19</text>
        <text x="242" y="408">Feb 20</text><text x="336" y="408">Mar 20</text>
        <text x="430" y="408">Nov 20</text>
      </g>
    </svg>
  </figure>
  <div class="page-no">04</div>
</section>

<section class="slide slide-5">
  <div class="brand brand-center">
    <div class="brand-mark"></div>
    <div class="brand-text"><div class="brand-name">OMO</div><div class="brand-sub">Osservatorio Marble Orchard</div></div>
  </div>
  <h2 class="closing thanks">Thank You</h2>
  <p class="closing closing-text">Fusce sollicitudin lorem et luctus volutpat. Proin placerat dapibus gravida. In tristique tristique nulla eget hendrerit. Maecenas vel tortor accumsan quam varius imperdiet vel eget elit. Aenean facilisis tincidunt lectus, id dictum nisi luctus eget. Vivamus efficitur ex condimentum, malesuada eros eget, feugiat nibh. Sed tellus ex, imperdiet eget gravida sit amet, volutpat eget turpis. In nec ultricies est. Etiam mattis augue vehicula odio posuere, sit amet tempus lectus luctus.</p>
  <div class="page-no">05</div>
</section>

</body>
</html>
```